Sable Grove products by Voldrin. Beauty, skin care cosmetic products

We are an all natural and organic beauty product company looking for a logo an label design ideas. Our motto is to make products that are safe, natural, in harmony with the earth and that really work. Our products will contribute to the transition from the Old Earth to the Sable Grove (as the image of the two worlds suggests). The earths can be mixed in the label. The label example is a rough sketch.
Updates

The label needs to be 1 (one) inch high and 7 inch long.

Need extra days to review

Target Market(s)

Products made with natural and organic ingredients. Beauty and skin products

Requirements
Must have
• My project must be standing out. We want customers to be draw to he product on the shelf. Wow, this label is different? what is it? All natural? I must try it.
• Must be bold but not outrageous.
• The two earth can be placed on right and left side of the tree of life on the second attachment
Nice to have
• The two Earth can be in the back ground suggesting that this product takes us from chemically and artificially filled products to something new that is in harmony with nature and health.
Should not have
• Should not be boring. Ordinary, easy to forget and ignore patterns, lettering, logos.

```html
<!DOCTYPE html>
<html lang="en">
<head>
<meta charset="utf-8">
<title>Sable Grove Products by Voldrin – Under-Arm-Balm Label</title>
<link rel="stylesheet" href="https://fonts.googleapis.com/css2?family=Cormorant+Garamond:wght@500;600&family=Open+Sans:wght@400;800&display=swap">
<style>
  :root {
    --page-bg: #ffffff;
    --variant-grey: #b3b4b6;
    --label-black: #07080c;
    --label-navy: #1c2a6e;
    --label-blue: #3a4fb4;
    --label-green: #1f4a36;
    --edge-blue: #4a5cc8;
    --brand-white: #f4f4f4;
    --product-green: #7cbf48;
    --scent-green: #6d9a3a;
  }
  * { margin: 0; padding: 0; box-sizing: border-box; }
  html, body {
    width: 1200px; height: 774px; overflow: hidden;
    background: var(--page-bg);
  }
  .canvas { position: relative; width: 1200px; height: 774px; }

  .variant-name {
    position: absolute;
    left: 180px; top: 383px;
    transform: translate(-50%, -50%) rotate(-90deg);
    font-family: "Open Sans", sans-serif;
    font-weight: 800;
    font-size: 112px;
    letter-spacing: 2px;
    color: var(--variant-grey);
    white-space: nowrap;
    line-height: 1;
  }

  .label {
    position: absolute;
    left: 295px; top: 256px;
    width: 650px; height: 372px;
    background: var(--label-black);
    overflow: hidden;
  }
  .label-artwork {
    position: absolute; inset: 0;
    background:
      radial-gradient(ellipse 120px 110px at 215px 180px, var(--label-navy) 0%, rgba(28,42,110,0.6) 55%, transparent 100%),
      radial-gradient(ellipse 120px 110px at 445px 180px, var(--label-navy) 0%, rgba(28,42,110,0.6) 55%, transparent 100%),
      radial-gradient(ellipse 300px 240px at 325px 200px, rgba(31,74,54,0.55) 0%, rgba(31,74,54,0.25) 60%, transparent 100%),
      linear-gradient(90deg, rgba(31,74,54,0.5) 0%, transparent 12%, transparent 86%, rgba(31,74,54,0.5) 96%, var(--edge-blue) 100%);
  }
  .scent-name {
    position: absolute;
    left: 2px; top: 186px;
    transform: translate(0, -50%) rotate(90deg);
    transform-origin: center;
    font-family: "Cormorant Garamond", serif;
    font-size: 20px;
    color: var(--scent-green);
    white-space: nowrap;
    width: 0;
  }
  .label-text {
    position: absolute; inset: 0;
    text-align: center;
    color: var(--brand-white);
  }
  .brand-name {
    position: absolute; left: 0; right: 0; top: 44px;
    font-family: "Cormorant Garamond", serif;
    font-weight: 600;
    font-size: 46px;
    line-height: 1;
  }
  .brand-maker {
    position: absolute; left: 0; right: 0; top: 100px;
    line-height: 1;
  }
  .brand-maker .by {
    font-family: "Cormorant Garamond", serif;
    font-weight: 600;
    font-size: 30px;
  }
  .brand-maker .maker {
    font-family: "Open Sans", sans-serif;
    font-weight: 800;
    font-size: 42px;
    color: #e6e6e6;
  }
  .product-name {
    position: absolute; left: 0; right: 0; top: 164px;
    font-family: "Open Sans", sans-serif;
    font-weight: 800;
    font-size: 48px;
    color: var(--product-green);
    line-height: 1;
  }
  .claim {
    position: absolute; left: 0; right: 0; top: 262px;
    font-family: "Cormorant Garamond", serif;
    font-weight: 500;
    font-size: 27px;
    line-height: 1;
  }
  .free-from {
    position: absolute; left: 0; right: 0; top: 302px;
    font-family: "Open Sans", sans-serif;
    font-size: 21px;
    line-height: 1;
  }
  .free-from b { font-weight: 800; }
</style>
</head>
<body>
<main class="canvas">
  <div class="variant-name">ORIGINAL</div>

  <section class="label">
    <div class="label-artwork" role="img" aria-label="Ornamental knotwork frame with two earths on either side of a tree of life, in deep navy, blue and green"></div>
    <div class="scent-name">Original Scent</div>
    <div class="label-text">
      <p class="brand-name">Sable Grove Products</p>
      <p class="brand-maker"><span class="by">by</span> <span class="maker">VOLDRIN</span></p>
      <h1 class="product-name">UNDER-ARM-BALM</h1>
      <p class="claim">100% NATURAL INGREDIENTS</p>
      <p class="free-from"><b>No</b> Aluminum, <b>No</b> Parabens, <b>No</b> Phthalates</p>
    </div>
  </section>
</main>
</body>
</html>
```